New Interrior Decoration company needs new website

We need a website for our new company specialising in interior decoration to residential and commercial markets.
We supply and install decorative and printed films for office and home decoration such as feature walls.
We would like to keep the design simple and clean.

Target Market(s)

Architects and interior designaers

Industry/Entity Type

It Company

Number of Pages Required

5+ page

Font styles to use
Sans Serif

Requirements
Must have
• Home page,
• Services/products page (split into commercial and residential)
• Gallery (split into commercial and residential)
• contact form and page
Nice to have
• Very clean and minimalistic design.

```html
<!DOCTYPE html>
<html lang="en">
<head>
<meta charset="utf-8">
<title>Linea Interiors</title>
<link href="https://fonts.googleapis.com/css2?family=Roboto:wght@400;500;700&family=Roboto+Condensed:wght@400;700&display=swap" rel="stylesheet">
<style>
:root{
  --blue:#0d5cb6;
  --blue-bar:#1565c8;
  --ink:#2b2b2b;
  --muted:#666;
  --light:#f4f4f4;
  --card:#f7f7f7;
  --dark:#1d1d1d;
  --white:#fff;
}
*{box-sizing:border-box;margin:0;padding:0}
html,body{width:1200px;height:3214px;overflow:hidden}
body{font-family:'Roboto',sans-serif;color:var(--ink);background:var(--white);position:relative}
.section{position:absolute;left:0;width:1200px}
.center{text-align:center}
.cond{font-family:'Roboto Condensed',sans-serif}

/* header */
.site-header{top:0;height:86px;background:var(--white);border-top:4px solid var(--blue)}
.brand{position:absolute;left:98px;top:20px;display:flex;align-items:center;gap:10px}
.brand-mark{width:46px;height:46px;background:var(--blue)}
.brand-name{font-family:'Roboto Condensed',sans-serif;font-weight:700;font-size:26px;line-height:24px;color:var(--ink);width:160px}
.nav{position:absolute;top:28px;left:581px;display:flex;align-items:center}
.nav a{font-size:13px;color:var(--ink);text-decoration:none;text-transform:uppercase;padding:8px 20px;height:30px}
.nav a.active{background:var(--blue);color:var(--white);padding:8px 24px}
.cart{position:absolute;left:1066px;top:30px;width:26px;height:26px;border-radius:50%;background:var(--blue)}
.cart-count{position:absolute;left:1085px;top:24px;width:12px;height:12px;border-radius:50%;background:#333;color:#fff;font-size:8px;text-align:center;line-height:12px}

/* hero */
.hero{top:86px;height:557px;background:linear-gradient(180deg,#4a4a48 0%,#2f2f2e 45%,#6b6b68 75%,#8c8c88 100%)}
.hero-title{position:absolute;top:250px;left:0;width:100%;font-size:58px;font-weight:700;color:var(--white)}
.hero-sub{position:absolute;top:318px;left:0;width:100%;font-size:19px;color:var(--white)}
.hero-arrow{position:absolute;top:262px}

/* welcome */
.welcome{top:643px;height:553px;background:var(--white)}
.section-title{font-family:'Roboto Condensed',sans-serif;font-weight:400;font-size:32px;color:var(--ink);text-transform:uppercase}
.section-title .accent{color:var(--blue)}
.welcome .section-title{position:absolute;top:44px;left:0;width:100%}
.intro{position:absolute;top:100px;left:172px;width:856px;font-size:11.5px;line-height:19px;color:#555}
.service{position:absolute;top:257px;width:311px;height:236px;background:var(--card);border:1px solid #ececec}
.service-icon{position:absolute;left:103px;top:-51px;width:104px;height:104px;border-radius:50%;background:var(--blue);border:4px solid #e6eef8;display:flex;align-items:center;justify-content:center}
.service h3{position:absolute;top:70px;left:0;width:100%;font-family:'Roboto Condensed',sans-serif;font-weight:400;font-size:18px;text-transform:uppercase}
.service p{position:absolute;top:103px;left:34px;width:243px;font-size:11.5px;line-height:17px;color:#666}
.service .rule{position:absolute;top:181px;left:115px;width:80px;height:1px;background:var(--blue)}
.service .more{position:absolute;top:194px;left:0;width:100%;text-align:center;font-size:11px;font-weight:700;color:var(--blue)}

/* supply band */
.supply{top:1196px;height:465px;background:linear-gradient(180deg,#2b2b2b 0%,#1a1a1a 55%,#2a2a2a 100%);color:var(--white)}
.supply h2{position:absolute;top:110px;left:0;width:100%;font-family:'Roboto Condensed',sans-serif;font-size:40px;font-weight:700}
.supply h3{position:absolute;top:154px;left:0;width:100%;font-family:'Roboto Condensed',sans-serif;font-size:25px;font-weight:400}
.supply .bar{position:absolute;top:199px;left:547px;width:106px;height:2px;background:var(--white)}
.supply p{position:absolute;top:224px;left:175px;width:850px;font-size:12px;line-height:22px}
.btn{display:inline-block;background:var(--blue);color:var(--white);font-size:14px;text-transform:uppercase}
.supply .btn{position:absolute;top:315px;left:534px;width:130px;height:34px;line-height:34px;border:1px solid #5a9ae0}

/* gallery */
.gallery{top:1661px;height:735px;background:var(--white)}
.gallery .section-title{position:absolute;top:52px;left:0;width:100%;font-size:30px}
.tile{position:absolute;display:flex;align-items:center;justify-content:center}
.tile-label{border:1px solid rgba(255,255,255,.8);color:var(--white);font-family:'Roboto Condensed',sans-serif;font-size:20px;padding:6px 18px;background:rgba(0,0,0,.2)}

/* blog */
.blog{top:2396px;height:476px;background:var(--light)}
.blog .section-title{position:absolute;top:36px;left:0;width:100%;font-size:30px}
.post{position:absolute;top:96px;width:310px}
.post-image{height:189px;position:relative}
.date{position:absolute;left:0;bottom:0;width:52px;height:56px;background:var(--blue);color:#fff;text-align:center;font-weight:700;font-size:20px;padding-top:8px;line-height:20px}
.date small{display:block;font-size:9px;font-weight:400}
.post h4{margin-top:18px;font-size:19px;font-weight:400;color:var(--ink)}
.post p{margin-top:8px;font-size:11.5px;line-height:17px;color:#666}
.post .more{margin-top:14px;font-size:12px;font-weight:500;color:var(--ink);display:flex;align-items:center;gap:6px}

/* footer */
.footer{top:2872px;height:295px;background:var(--dark);color:#ddd}
.footer h5{position:absolute;top:55px;font-family:'Roboto Condensed',sans-serif;font-size:18px;font-weight:400;color:#fff;text-transform:uppercase}
.links{position:absolute;left:98px;top:90px;list-style:none}
.links li{font-size:12.5px;height:22.5px;display:flex;align-items:center;gap:12px}
.contact{position:absolute;left:285px;top:90px;font-size:12.5px;line-height:19px}
.contact-row{display:flex;gap:12px;margin-bottom:14px}
.socials{display:flex;gap:8px}
.socials span{width:20px;height:20px;border:1px solid #aaa;border-radius:50%}
.quote{position:absolute;left:634px;top:90px;width:465px}
.quote p{font-size:12px;line-height:19px}
.field{position:absolute;width:225px;height:41px;border:1px solid #444;background:#1a1a1a;color:#888;font-size:11px;padding:13px 14px}
.signup{position:absolute;left:247px;top:118px;width:218px;height:41px;line-height:41px;text-align:center;background:var(--blue);color:#fff;font-size:15px;text-transform:uppercase}
.copyright{top:3167px;height:47px;background:var(--blue-bar);color:#fff;font-size:12px;line-height:47px;text-align:center}
</style>
</head>
<body>

<header class="section site-header">
  <div class="brand"><span class="brand-mark"></span><span class="brand-name">LINEA INTERIORS</span></div>
  <nav class="nav">
    <a class="active" href="#">Home</a><a href="#">Services</a><a href="#">Products</a><a href="#">Gallery</a><a href="#">Contact Us</a>
  </nav>
  <span class="cart"></span>
  <svg style="position:absolute;left:1071px;top:36px" width="16" height="14" viewBox="0 0 16 14"><path d="M1 1h3l2 8h8l1.5-6H5" fill="none" stroke="#fff" stroke-width="1.5"/><circle cx="7" cy="12" r="1.3" fill="#fff"/><circle cx="13" cy="12" r="1.3" fill="#fff"/></svg>
  <span class="cart-count">0</span>
</header>

<section class="section hero" role="img" aria-label="Photo of a modern open kitchen interior with pendant lights">
  <svg class="hero-arrow" style="left:36px" width="26" height="56" viewBox="0 0 26 56"><path d="M24 2L2 28l22 26" fill="none" stroke="rgba(255,255,255,.7)" stroke-width="2"/></svg>
  <svg class="hero-arrow" style="left:1138px" width="26" height="56" viewBox="0 0 26 56"><path d="M2 2l22 26L2 54" fill="none" stroke="rgba(255,255,255,.7)" stroke-width="2"/></svg>
  <h1 class="hero-title center cond">LINEA INTERIORS</h1>
  <p class="hero-sub center">We specialise in interior decoration to residential and commercial markets.</p>
</section>

<section class="section welcome">
  <h2 class="section-title center">Welcome to <span class="accent">Linea Interiors</span></h2>
  <p class="intro center">Lorem ipsum dolor sit amet, consectetur adipiscing elit, sed do eiusmod tempor incididunt ut labore et dolore magna aliqua. Ut enim ad minim veniam, quis nostrud exercitation ullamco laboris nisi ut aliquip ex ea commodo consequat. Duis aute irure dolor in reprehenderit in voluptate velit esse cillum dolore eu fugiat nulla pariatur. Excepteur sint occaecat cupidatat non proident, sunt in culpa qui officia deserunt mollit anim id est laborum</p>

  <article class="service center" style="left:98px">
    <div class="service-icon"><svg width="46" height="46" viewBox="0 0 46 46" fill="none" stroke="#fff" stroke-width="2.5"><rect x="4" y="4" width="9" height="9"/><rect x="33" y="4" width="9" height="9"/><rect x="4" y="33" width="9" height="9"/><rect x="33" y="33" width="9" height="9"/><path d="M13 8h20M8 13v20M13 38h20M38 13v20"/></svg></div>
    <h3>Remodeling</h3>
    <p>Neque porro quisquam est, qui dolorem ipsum quia dolor sit amet, consectetur, adipisci velit, sed quia non numquam eius modi tempora</p>
    <span class="rule"></span><span class="more">READ MORE INFO</span>
  </article>
  <article class="service center" style="left:441px">
    <div class="service-icon"><svg width="46" height="46" viewBox="0 0 46 46" fill="#fff"><path d="M23 4L3 22h6v20h28V22h6z"/><rect x="15" y="26" width="6" height="6" fill="#0d5cb6"/><rect x="25" y="26" width="6" height="6" fill="#0d5cb6"/><rect x="20" y="34" width="6" height="8" fill="#0d5cb6"/></svg></div>
    <h3>Residential</h3>
    <p>Neque porro quisquam est, qui dolorem ipsum quia dolor sit amet, consectetur, adipisci velit, sed quia non numquam eius modi tempora</p>
    <span class="rule"></span><span class="more">READ MORE INFO</span>
  </article>
  <article class="service center" style="left:786px">
    <div class="service-icon"><svg width="46" height="46" viewBox="0 0 46 46" fill="#fff"><rect x="6" y="14" width="14" height="28"/><rect x="22" y="4" width="18" height="38"/><g fill="#0d5cb6"><rect x="9" y="18" width="3" height="3"/><rect x="14" y="18" width="3" height="3"/><rect x="9" y="25" width="3" height="3"/><rect x="14" y="25" width="3" height="3"/><rect x="26" y="9" width="3" height="3"/><rect x="33" y="9" width="3" height="3"/><rect x="26" y="17" width="3" height="3"/><rect x="33" y="17" width="3" height="3"/><rect x="26" y="25" width="3" height="3"/><rect x="33" y="25" width="3" height="3"/></g></svg></div>
    <h3>Commercial Markets</h3>
    <p>Neque porro quisquam est, qui dolorem ipsum quia dolor sit amet, consectetur, adipisci velit, sed quia non numquam eius modi tempora</p>
    <span class="rule"></span><span class="more">READ MORE INFO</span>
  </article>
</section>

<section class="section supply center" role="img" aria-label="Darkened photo of a modern interior behind the text">
  <h2>WE SUPPLY AND INSTALL DECORATIVE</h2>
  <h3>AND PRINTED FILMS FOR OFFICE AND HOME DECORATION SUCH AS FEATURE WALLS</h3>
  <span class="bar"></span>
  <p>Lorem ipsum dolor sit amet, consectetur adipiscing elit, sed do eiusmod tempor incididunt ut labore et dolore magna aliqua. Ut enim ad minim veniam, quis nostrud exercitation ullamco laboris nisi ut aliquip ex ea commodo consequat. Duis aute irure dolor in reprehenderit in voluptate velit esse cillum dolore eu fugiat nulla pariatur. Excepteur sint occaecat cupidatat non proident, sunt in culpa qui officia deserunt mollit</p>
  <span class="btn">Read More</span>
</section>

<section class="section gallery">
  <h2 class="section-title center">Linea Interiors Gallery</h2>
  <div class="tile" style="left:98px;top:124px;width:307px;height:268px;background:linear-gradient(160deg,#5a2e33,#3a2a2a 60%,#9a9088)" role="img" aria-label="Remodeled living room with dark red feature wall"><span class="tile-label">REMODELING</span></div>
  <div class="tile" style="left:418px;top:124px;width:306px;height:268px;background:linear-gradient(160deg,#6a6e6c,#3a3f3e 60%,#2a2d2c)" role="img" aria-label="Grey interior with pendant lamps"><span class="tile-label">INTERIORS</span></div>
  <div class="tile" style="left:735px;top:124px;width:364px;height:547px;background:linear-gradient(170deg,#b8c08a,#d7dc7a 45%,#c9c9b8 70%,#9a9a92)" role="img" aria-label="Residential room with yellow-green patterned feature wall and armchair"><span class="tile-label">NEW RESIDENTIAL</span></div>
  <div class="tile" style="left:98px;top:405px;width:307px;height:266px;background:linear-gradient(160deg,#7a3f2c,#4a4a48 55%,#8a8378)" role="img" aria-label="Commercial space with brick wall and shelving"><span class="tile-label">COMMERCIAL</span></div>
  <div class="tile" style="left:418px;top:405px;width:306px;height:266px;background:linear-gradient(180deg,#6c7060,#4e5a3e 55%,#5f7a3a)" role="img" aria-label="Landscape scene with grass lawn"><span class="tile-label">LANDSCAPE</span></div>
</section>

<section class="section blog">
  <h2 class="section-title center">Latest Blog</h2>
  <article class="post" style="left:98px">
    <div class="post-image" style="background:linear-gradient(135deg,#6a2e20,#3a1a18 55%,#c9a0b0)" role="img" aria-label="Interior with pink lounge chair and lamp"><span class="date">02<small>JUN</small></span></div>
    <h4>Lorem ipsum dolor sit amet,</h4>
    <p>Lorem ipsum dolor sit amet, consectetur adipiscing elit. Sed blandit massa vel mauris sollicitudin dignissim. Lorem ipsum dolor sit amet, consectetur</p>
    <span class="more">READ MORE <svg width="10" height="10" viewBox="0 0 10 10"><circle cx="5" cy="5" r="5" fill="#2b2b2b"/><path d="M4 3l2 2-2 2" stroke="#fff" fill="none"/></svg></span>
  </article>
  <article class="post" style="left:443px">
    <div class="post-image" style="background:linear-gradient(160deg,#6e7670,#555d58 55%,#b8b2a8)" role="img" aria-label="Grey wall with framed art above a white sideboard"><span class="date">02<small>JUN</small></span></div>
    <h4>Lorem ipsum dolor sit amet,</h4>
    <p>Lorem ipsum dolor sit amet, consectetur adipiscing elit. Sed blandit massa vel mauris sollicitudin dignissim. Lorem ipsum dolor sit amet, consectetur</p>
    <span class="more">READ MORE <svg width="10" height="10" viewBox="0 0 10 10"><circle cx="5" cy="5" r="5" fill="#2b2b2b"/><path d="M4 3l2 2-2 2" stroke="#fff" fill="none"/></svg></span>
  </article>
  <article class="post" style="left:791px">
    <div class="post-image" style="background:linear-gradient(150deg,#b89aa8,#8a7aa0 50%,#c8a8b0)" role="img" aria-label="Colourful printed film wall"><span class="date">02<small>JUN</small></span></div>
    <h4>Lorem ipsum dolor sit amet,</h4>
    <p>Lorem ipsum dolor sit amet, consectetur adipiscing elit. Sed blandit massa vel mauris sollicitudin dignissim. Lorem ipsum dolor sit amet, consectetur</p>
    <span class="more">READ MORE <svg width="10" height="10" viewBox="0 0 10 10"><circle cx="5" cy="5" r="5" fill="#2b2b2b"/><path d="M4 3l2 2-2 2" stroke="#fff" fill="none"/></svg></span>
  </article>
</section>

<footer class="section footer">
  <h5 style="left:98px">Quick Link</h5>
  <ul class="links">
    <li>›<span>Home</span></li><li>›<span>About</span></li><li>›<span>Our Products</span></li><li>›<span>Services</span></li><li>›<span>News</span></li><li>›<span>Contact us</span></li>
  </ul>
  <h5 style="left:285px">Contacts</h5>
  <div class="contact">
    <div class="contact-row"><svg width="12" height="16" viewBox="0 0 12 16"><path d="M6 1a5 5 0 0 0-5 5c0 4 5 9 5 9s5-5 5-9a5 5 0 0 0-5-5z" fill="none" stroke="#ddd" stroke-width="1.4"/><circle cx="6" cy="6" r="1.8" fill="#ddd"/></svg><span>Linea Interiors<br>PO Box 470215 1820 Harbor Crest Way<br>Bayfield, CA 90410</span></div>
    <div class="contact-row" style="font-size:14px"><svg width="14" height="14" viewBox="0 0 14 14"><path d="M3 1l2 3-1.5 1.5a8 8 0 0 0 5 5L10 9l3 2-1.5 2.5C6 13 1 8 .8 2.5z" fill="#ddd"/></svg><span>Call Us: 1-800-555-0142</span></div>
    <div class="contact-row"><svg width="14" height="12" viewBox="0 0 14 12"><rect x="1" y="1" width="12" height="10" fill="none" stroke="#ddd" stroke-width="1.4"/><path d="M1 1l6 5 6-5" fill="none" stroke="#ddd" stroke-width="1.4"/></svg><span>hello@lineainteriors.example</span></div>
    <div class="socials"><span></span><span></span><span></span><span></span></div>
  </div>
  <h5 style="left:634px">Get a Free Quote</h5>
  <div class="quote">
    <p>Lorem ipsum dolor sit amet, consectetur adipiscing elit, sed do eiusmod tempor incididunt ut labore et dolore magna aliqua. Ut enim ad minim veniam,</p>
    <span class="field" style="left:0;top:62px">Name</span>
    <span class="field" style="left:247px;top:62px;width:218px">E - Mail</span>
    <span class="field" style="left:0;top:118px">Phone No</span>
    <span class="signup">Signup Now</span>
  </div>
</footer>

<div class="section copyright">© 2016 Linea Interiors . All Rights Reserved.</div>

</body>
</html>
```